Business card design needed

Family General Practitioner/ Family Physician.
Logo is the logo of the Noble Guild of Family Healers Oceania
http://kpltw.varendo.example/ImageShelf/marks/pages/NGFHO%20mark_jpg.htm
Updates

Project Deadline Extended
Reason: Just a bit more time to make changes and the weekend for me to look at things closely and to choose. Thanks, Orin

Thanks for all the submissions. So many of them are really works of art. Not one of them are not good. The ones that I am eliminating are the ones that I think are not suitable for me personally only, and because if I don't, it makes it very difficult to decide as many of you are also sending me slight variations of a card. I have just decided to choose a second place card too. Can't thank you all enough. Good luck, Orin. P.S - Working today till 10 pm as the card says :-), so probably won't be able to give a feedback till late Saturday night or Sunday morning here in Sydney, Australia. 

Project Deadline Extended
Reason: Just added a second place to the budget and realised that Australia is ahead of the rest of the world in the time zone (only :-) - don't want to offend anyone or start a debate!! ) , so Monday deadline will mean it will be a weekend for the rest of the world. Just wanted to give everyone more time to submit their best, especially since I will be picking a second card too. Can't thank everyone enough for the submissions. P.S - Not keen on photos on the card.

Industry/Entity Type

Business

Contact Information for Business Card

Dr. Orin Halvey M.B.B.S., F.N.G.F.H.O
Family General Practitioner
Address, timings, phone and fax number on the back.

Requirements
Must have
• Timings
Mon 7 am - 7 pm
Tues 7 am - 12 pm
Wed 7 am - 10 pm
Thurs 7 am - 12 pm
Fri 7 am - 8 pm
Sat 8 am - 10 pm
Sun - Off

```html
<!DOCTYPE html>
<html lang="en">
<head>
<meta charset="utf-8">
<title>Dr. Orin Halvey – Business Card</title>
<link rel="stylesheet" href="https://fonts.googleapis.com/css2?family=Cutive&family=PT+Sans:wght@400;700&display=swap">
<style>
  :root {
    --backdrop: #ece4d6;
    --card-blue: #4f80bf;
    --pulse-yellow: #f4c20d;
    --pulse-blue: #4a7cc0;
    --card-white: #ffffff;
    --ink-white: #ffffff;
    --ink-grey: #4a4a4a;
    --ink-dark: #1e1e1e;
  }
  * { margin: 0; padding: 0; box-sizing: border-box; }
  html, body { width: 1200px; height: 417px; overflow: hidden; }
  body { background: var(--backdrop); position: relative; }

  .card { position: absolute; top: 68px; height: 304px; overflow: hidden; }
  .card-front { left: 55px; width: 545px; background: var(--card-blue); color: var(--ink-white); font-family: "Cutive", serif; }
  .card-back { left: 623px; width: 534px; background: var(--card-white); }

  .pulse { position: absolute; left: 0; top: 0; }

  .guild-name {
    position: absolute; left: 22px; top: 40px; width: 112px;
    font-family: "Cutive", serif; font-size: 11px; line-height: 15px;
    text-align: center; color: var(--ink-white);
  }
  .doctor-name { position: absolute; left: 223px; top: 50px; font-size: 33px; line-height: 40px; white-space: nowrap; }
  .credentials { position: absolute; left: 223px; top: 96px; font-size: 13px; letter-spacing: 1.5px; }
  .role { position: absolute; left: 223px; top: 193px; font-size: 18px; white-space: nowrap; }

  .hours-title {
    position: absolute; left: 0; width: 100%; top: 27px; text-align: center;
    font-family: "Cutive", serif; font-size: 16px; color: var(--ink-grey);
  }
  .hours { position: absolute; left: 233px; top: 57px; border-collapse: collapse; color: var(--ink-grey); }
  .hours td { height: 16.6px; padding: 0; font-size: 13px; line-height: 16px; vertical-align: middle; }
  .hours .day { font-family: "Cutive", serif; font-weight: bold; width: 80px; }
  .hours .sep { font-family: "PT Sans", sans-serif; width: 20px; }
  .hours .time { font-family: "PT Sans", sans-serif; font-size: 12.5px; white-space: pre; }

  .address {
    position: absolute; left: 235px; top: 216px;
    font-family: "PT Sans", sans-serif; font-size: 12.5px; line-height: 18.5px; color: var(--ink-dark);
  }
  .address b { font-weight: 700; }
</style>
</head>
<body>
  <section class="card card-front">
    <div class="guild-name">Noble Guild of Family Healers Oceania</div>
    <h1 class="doctor-name" style="font-weight:normal">Dr. Orin Halvey</h1>
    <p class="credentials">M.B.B.S., F.N.G.F.H.O</p>
    <svg class="pulse" width="545" height="304" viewBox="0 0 545 304" aria-hidden="true">
      <polyline points="0,225 85,225 96,195 106,224 140,154 153,262 169,194 181,225 545,225"
        fill="none" stroke="var(--pulse-yellow)" stroke-width="4" stroke-linejoin="miter"/>
    </svg>
    <p class="role">Family General Practitioner</p>
  </section>

  <section class="card card-back">
    <h2 class="hours-title" style="font-weight:normal">Working Hours</h2>
    <table class="hours">
      <tr><td class="day">Monday</td><td class="sep">:</td><td class="time">7 AM -  7 PM</td></tr>
      <tr><td class="day">Tuesday</td><td class="sep">:</td><td class="time">7 AM - 12 PM</td></tr>
      <tr><td class="day">Wednesday</td><td class="sep">:</td><td class="time">7 AM - 10 PM</td></tr>
      <tr><td class="day">Thursday</td><td class="sep">:</td><td class="time">7 AM - 12 PM</td></tr>
      <tr><td class="day">Friday</td><td class="sep">:</td><td class="time">7 AM -  8 PM</td></tr>
      <tr><td class="day">Saturday</td><td class="sep">:</td><td class="time">8 AM - 10 PM</td></tr>
      <tr><td class="day">Sunday</td><td class="sep">:</td><td class="time">OFF</td></tr>
    </table>
    <svg class="pulse" width="534" height="304" viewBox="0 0 534 304" aria-hidden="true">
      <polyline points="0,198 84,198 97,168 113,210 140,126 153,232 168,166 183,198 534,198"
        fill="none" stroke="var(--pulse-blue)" stroke-width="4" stroke-linejoin="miter"/>
    </svg>
    <address class="address" style="font-style:normal">
      Upper Level, Arbor Court,<br>
      Linden Square Shopping Centre,<br>
      Marrow Hill, NSW 2199<br>
      <b>P :</b> 02 5550 1400 <b>F :</b> 02 5550 1233
    </address>
  </section>
</body>
</html>
```